Vantiqo custom business card design

Need a authentic, innovative business card design for a new mobile app business. I am uploading a few screen images from our app for you to view. I would like app design theme to match business card design. I can also send logo images.

```html
<!DOCTYPE html>
<html lang="en">
<head>
<meta charset="utf-8">
<title>Vantiqo Business Card</title>
<link rel="stylesheet" href="https://fonts.googleapis.com/css2?family=Montserrat:wght@700;800&family=Open+Sans:wght@400;600&display=swap">
<style>
  :root {
    --stage: #e8e6ea;
    --card-light: #f7f5f6;
    --card-dark: #1e1e1e;
    --accent: #6c1599;
    --accent-name: #7a22ad;
    --text-light: #ffffff;
    --text-dark: #1c1c1c;
  }
  * { margin: 0; padding: 0; box-sizing: border-box; }
  html, body {
    width: 1200px;
    height: 900px;
    overflow: hidden;
    background: var(--stage);
  }
  .business-card {
    position: absolute;
    left: 165px;
    top: 182px;
    width: 870px;
    height: 536px;
    background: var(--card-light);
    overflow: hidden;
    box-shadow: 0 10px 30px rgba(0,0,0,0.12);
    font-family: "Open Sans", Arial, sans-serif;
  }
  .dark-panel {
    position: absolute;
    inset: 0;
    width: 870px;
    height: 536px;
  }
  .contact-block {
    position: absolute;
    left: 43px;
    top: 0;
    color: var(--text-light);
  }
  .person-name {
    position: absolute;
    top: 175px;
    white-space: nowrap;
    font-family: "Montserrat", Arial, sans-serif;
    font-weight: 800;
    font-size: 29px;
    line-height: 34px;
    color: var(--accent-name);
    letter-spacing: 0.2px;
  }
  .person-title {
    position: absolute;
    top: 209px;
    white-space: nowrap;
    font-size: 24px;
    line-height: 30px;
  }
  .contact-list {
    position: absolute;
    top: 274px;
    list-style: none;
    white-space: nowrap;
  }
  .contact-list li {
    display: flex;
    align-items: center;
    gap: 6px;
    font-size: 24px;
    line-height: 31.5px;
  }
  .contact-icon {
    width: 20px;
    height: 20px;
    flex: none;
    fill: var(--accent);
  }
  .postal-address {
    position: absolute;
    top: 423px;
    white-space: nowrap;
    font-style: normal;
    font-size: 23px;
    line-height: 31px;
  }
  .brand-mark {
    position: absolute;
    left: 520px;
    top: 0;
    width: 350px;
    height: 536px;
    display: flex;
    align-items: center;
    justify-content: center;
    gap: 14px;
  }
  .brand-dot {
    width: 30px;
    height: 30px;
    border-radius: 50%;
    background: var(--accent);
  }
  .brand-name {
    font-family: "Montserrat", Arial, sans-serif;
    font-weight: 800;
    font-size: 62px;
    color: var(--text-dark);
  }
</style>
</head>
<body>
  <div class="business-card">
    <svg class="dark-panel" viewBox="0 0 652 402" preserveAspectRatio="none" aria-hidden="true">
      <path d="M0 0 H165 Q232 8 268 100 Q332 112 360 160 Q382 222 328 268 Q300 296 292 330 Q274 388 252 402 H0 Z"
            fill="var(--card-dark)" stroke="var(--accent)" stroke-width="3"/>
    </svg>

    <div class="contact-block">
      <h1 class="person-name">MARCUS ELLERY</h1>
      <p class="person-title">Managing Director</p>
      <ul class="contact-list">
        <li>
          <svg class="contact-icon" viewBox="0 0 20 20"><path d="M2 8 Q10 2 18 8 L16 10 L13 8 V6.5 Q10 5.5 7 6.5 V8 L4 10 Z M5 11 H15 L16 17 H4 Z"/></svg>
          021-555 310 482
        </li>
        <li>
          <svg class="contact-icon" viewBox="0 0 20 20"><path d="M6 1 H14 Q15 1 15 2 V18 Q15 19 14 19 H6 Q5 19 5 18 V2 Q5 1 6 1 Z M7 3 V15 H13 V3 Z M9 16 H11 V17.5 H9 Z"/></svg>
          021-555 310 482
        </li>
        <li>
          <svg class="contact-icon" viewBox="0 0 20 20"><path d="M2 4 H18 V16 H2 Z M3 5 L10 11 L17 5" stroke="var(--card-dark)" stroke-width="1.2"/></svg>
          hello@vantiqo-app.com
        </li>
        <li>
          <svg class="contact-icon" viewBox="0 0 20 20"><circle cx="10" cy="10" r="8"/><path d="M6 6 Q9 7 8 10 Q11 11 10 15 M12 4 Q13 7 15 8" stroke="var(--card-dark)" stroke-width="1.3" fill="none"/></svg>
          www.vantiqo-app.com
        </li>
      </ul>
      <address class="postal-address">
        48 Harbour Lane, Suite 7<br>
        Westbridge, 204518
      </address>
    </div>

    <div class="brand-mark">
      <span class="brand-dot"></span>
      <span class="brand-name">Vantiqo</span>
    </div>
  </div>
</body>
</html>
```